Launching a new real estate agency in Monaco

Hello, I am opening a new real estate agency in Monaco. For the purpose of my activity, in order to be known quickly among a fierce competition I need an advertising campaign that will be broadcast in local magazines, newspapers, paper board, etc.

You will find example of pictures of Monaco on which I have the rights and my logo. You can always pick other images that I can buy if the price is reasonable for a commercial use (<200 $)

Please respect the color code.

I wish you good luck and look forward to give you my feedbacks

Reason: Only few projects posted were respecting the brief and of quality. Hoping to receive more in coming days

Target Market(s)

International high-end clientele of all ages, all genders.

Industry/Entity Type

Real Estate Agent

Font styles to use
Serif

Requirements
Must have
• 1/ My logo
• 2/ This message "Un nouveau regard sur l'immobilier" means in English a fresh look at real estate or new eyes on real-estate.
• 3/ My address: 14 rue des Ormeaux, Galerie Bellerive Nord, 98 000 Monaco
• 4/ Phone number: +377.93.48.25.07
• 5/ Website: www.corvano-immo.com.
• 6/ Format: Files should be easily adjustable but I'd like a vertical display to fit easily in Magazines, Poster and billboard. So please work in high resolution !
Nice to have
• Please think about your design in accordance with the message I want to display.
Should not have
• A simple poster with a picture of Monaco that does not take into consideration the message of the advertisement, "Un nouveau regard sur l'immobilier" which means in english, new eyes on real-estate or a new look at real-estate, or new vision at real-estate.

```html
<!DOCTYPE html>
<html lang="fr">
<head>
<meta charset="utf-8">
<title>Corvano – Un nouveau regard sur l'immobilier</title>
<link href="https://fonts.googleapis.com/css2?family=Abril+Fatface&family=Arimo:wght@400;700&display=swap" rel="stylesheet">
<style>
  :root {
    --page: #ffffff;
    --navy: #2d4059;
    --rose: #e8a796;
    --white: #ffffff;
  }
  html, body {
    margin: 0;
    padding: 0;
    width: 1200px;
    height: 1200px;
    overflow: hidden;
    background: var(--page);
  }
  .poster {
    position: absolute;
    left: 233px;
    top: 50px;
    width: 734px;
    height: 1100px;
    background: var(--navy);
  }
  .website {
    position: absolute;
    top: 76px;
    left: 0;
    width: 100%;
    text-align: center;
    font-family: "Arimo", Arial, sans-serif;
    font-size: 20px;
    color: var(--rose);
    letter-spacing: 0.2px;
  }
  .viewfinder {
    position: absolute;
    left: 0;
    top: 0;
    width: 734px;
    height: 560px;
  }
  .rule {
    position: absolute;
    left: 91px;
    width: 551px;
    height: 2px;
    background: var(--white);
  }
  .rule--top { top: 581px; }
  .rule--mid { top: 902px; }
  .rule--bottom { top: 1037px; }
  .headline {
    position: absolute;
    top: 628px;
    left: 0;
    width: 100%;
    margin: 0;
    text-align: center;
    font-family: "Abril Fatface", "Bodoni Moda", serif;
    font-weight: 400;
    font-size: 76px;
    line-height: 80px;
    color: var(--white);
    letter-spacing: 1px;
  }
  .brand {
    position: absolute;
    left: 91px;
    top: 948px;
    font-family: "Abril Fatface", serif;
    font-size: 40px;
    line-height: 50px;
    color: var(--rose);
    letter-spacing: 3px;
  }
  .contact {
    position: absolute;
    left: 424px;
    top: 946px;
    font-family: "Arimo", Arial, sans-serif;
    color: var(--rose);
  }
  .contact__phone {
    font-size: 17px;
    font-weight: 700;
    line-height: 20px;
    margin: 0 0 3px;
  }
  .contact__address {
    font-size: 11.5px;
    line-height: 14px;
    margin: 0;
  }
</style>
</head>
<body>
  <main class="poster">
    <div class="website">www.corvano-immo.com</div>

    <svg class="viewfinder" viewBox="0 0 734 560" xmlns="http://www.w3.org/2000/svg">
      <defs>
        <linearGradient id="coastTones" x1="0" y1="0" x2="0" y2="1">
          <stop offset="0" stop-color="#c9ccd8"/>
          <stop offset="0.35" stop-color="#7f9a6e"/>
          <stop offset="0.6" stop-color="#d9a477"/>
          <stop offset="0.75" stop-color="#5fc4d6"/>
          <stop offset="1" stop-color="#8fd8e0"/>
        </linearGradient>
        <clipPath id="lenses">
          <circle cx="197" cy="368" r="166"/>
          <circle cx="536" cy="368" r="166"/>
        </clipPath>
      </defs>
      <g role="img" aria-label="Vue panoramique de la côte de Monaco, ville et montagne au-dessus de la mer, vue à travers des jumelles">
        <rect x="0" y="180" width="734" height="380" fill="url(#coastTones)" clip-path="url(#lenses)"/>
      </g>
      <g class="crosshair" stroke="#ffffff" stroke-width="4">
        <line x1="366" y1="295" x2="366" y2="453"/>
        <line x1="287" y1="373" x2="443" y2="373"/>
      </g>
    </svg>

    <div class="rule rule--top"></div>
    <h1 class="headline">UN NOUVEAU<br>REGARD SUR<br>L'IMMOBILIER</h1>
    <div class="rule rule--mid"></div>

    <div class="brand">CORVANO</div>
    <div class="contact">
      <p class="contact__phone">+377.93.48.25.07</p>
      <p class="contact__address">14 rue des Ormeaux, Galerie Bellerive Nord<br>98 000 Monaco</p>
    </div>

    <div class="rule rule--bottom"></div>
  </main>
</body>
</html>
```